Looking for a modern, Professional business card design

We have a simple business card, but are looking for a more modern, professional look. A sample of the basic card is attached as well as the logo. We would also like to add that we offer:
Struggling with your finances?
- Learn to become debt free
- Discover the power of cash
- Control your money instead of it controlling you
Let us help you achieve a new level of financial freedom!
Also, we would like to have a "SPECIAL OFFER!: FREE 30 minute consultation"
Financial Planning

```html
<!DOCTYPE html>
<html lang="en">
<head>
<meta charset="utf-8">
<title>Ridgeway Money Coaching – Business Card</title>
<link rel="stylesheet" href="https://fonts.googleapis.com/css2?family=Source+Sans+3:ital,wght@0,400;0,600;1,600&display=swap">
<style>
  :root {
    --backdrop: #2e2e2e;
    --card: #111111;
    --card-edge: #1c1c1c;
    --green: #7cc242;
    --green-deep: #4fa32c;
    --white: #f2f2f2;
    --divider: #3a3a3a;
  }
  * { box-sizing: border-box; margin: 0; padding: 0; }
  html, body {
    width: 1200px; height: 900px; overflow: hidden;
    background: var(--backdrop);
    font-family: "Source Sans 3", sans-serif;
  }
  .stage { position: relative; width: 1200px; height: 900px; }
  .card {
    position: absolute; top: 305px;
    width: 500px; height: 290px;
    background: var(--card);
    border: 1px solid var(--card-edge);
    border-radius: 18px;
    box-shadow: 0 14px 30px rgba(0,0,0,.45);
    overflow: hidden;
  }
  .card--back { left: 70px; }
  .card--front { left: 630px; display: flex; align-items: center; justify-content: center; }

  /* back side */
  .pitch {
    position: absolute; left: 26px; top: 48px; width: 240px;
    text-align: right; color: var(--white); font-size: 15px; line-height: 1.3;
  }
  .pitch__headline { color: var(--green); font-weight: 600; font-size: 16px; text-align: left; margin-bottom: 2px; }
  .pitch__list { list-style: none; }
  .pitch__list li:last-child { margin-top: 8px; }
  .pitch__cta { color: var(--green-deep); font-style: italic; font-weight: 600; margin-top: 14px; }
  .offer { margin-top: 10px; }
  .offer__label { color: var(--green); font-size: 16px; }
  .offer__detail { font-weight: 600; font-size: 16px; }

  .divider {
    position: absolute; left: 280px; top: 54px; width: 1px; height: 92px;
    background: var(--divider);
  }
  .contact { position: absolute; left: 294px; right: 24px; top: 50px; color: var(--white); }
  .contact__name { color: var(--green); font-size: 17px; font-weight: 600; }
  .contact__role { font-size: 13px; margin-bottom: 16px; }
  .contact__list { list-style: none; font-size: 12.5px; line-height: 1.55; }
  .contact__list li { display: flex; align-items: center; gap: 7px; white-space: nowrap; }
  .contact__list svg { width: 10px; height: 10px; fill: var(--green); flex: none; }

  /* front side */
  .brand { display: flex; align-items: center; gap: 12px; }
  .brand__dot { width: 22px; height: 22px; border-radius: 50%; background: var(--green); }
  .brand__name { color: var(--green); font-weight: 600; font-size: 26px; letter-spacing: .5px; }
</style>
</head>
<body>
<main class="stage">
  <section class="card card--back" aria-label="Card back">
    <div class="pitch">
      <p class="pitch__headline">Struggling with your finances?</p>
      <ul class="pitch__list">
        <li>Learn to become debt free</li>
        <li>Discover the power of cash</li>
        <li>Control your money<br>instead of it controlling you</li>
      </ul>
      <p class="pitch__cta">Let us help you achieve a new<br>level of financial freedom!</p>
      <div class="offer">
        <p class="offer__label">SPECIAL OFFER!</p>
        <p class="offer__detail">FREE 30 minute consultation</p>
      </div>
    </div>
    <div class="divider"></div>
    <div class="contact">
      <p class="contact__name">Daniel R. Hale</p>
      <p class="contact__role">Personal Financial Coach</p>
      <ul class="contact__list">
        <li><svg viewBox="0 0 10 10" aria-hidden="true"><path d="M2 0.5 L3.6 2.8 L2.8 3.8 Q4 6.2 6.2 7.2 L7.2 6.4 L9.5 8 L8.2 9.5 Q1 8.4 0.5 1.8 Z"/></svg>(205) 555-0148</li>
        <li><svg viewBox="0 0 10 10" aria-hidden="true"><path d="M0 2 H10 V8.5 H0 Z M0.6 2.4 L5 5.6 L9.4 2.4" stroke="#111" stroke-width=".7"/></svg>daniel@ridgewaycoach.com</li>
        <li><svg viewBox="0 0 10 10" aria-hidden="true"><circle cx="5" cy="5" r="4.6"/><path d="M0.5 5 H9.5 M5 0.4 V9.6 M5 0.4 Q2 5 5 9.6 M5 0.4 Q8 5 5 9.6" stroke="#111" stroke-width=".7" fill="none"/></svg>www.ridgewaycoach.com</li>
      </ul>
    </div>
  </section>

  <section class="card card--front" aria-label="Card front">
    <div class="brand">
      <span class="brand__dot"></span>
      <span class="brand__name">Ridgeway Money Coaching</span>
    </div>
  </section>
</main>
</body>
</html>
```